Business Card Design For A Renovation Contractor Company

We need a business card for a new company based in Singapore, our company name is "RB Tolvane". We are a renovation contractor that builds designs into reality. We build more of F&B restaurants, retail stores and commercial offices. We work very closely with designers. The final design should communicate to our client that we are a company that you can trust, that will plan and complete your project without giving you a headache. I like my client to remember my company as "RB". The beauty of SIMPLE is important.

Industry/Entity Type

Contractor

Requirements
Nice to have
• Black or Red base

```html
<!DOCTYPE html>
<html lang="en">
<head>
<meta charset="utf-8">
<title>RB Tolvane – Business Card</title>
<link href="https://fonts.googleapis.com/css2?family=Open+Sans:wght@300;400;600;700&display=swap" rel="stylesheet">
<style>
  :root {
    --ink: #111111;
    --red: #e01e25;
    --white: #ffffff;
    --text: #3a3a3a;
    --rule: #cfcfcf;
    --stage: #e9e9ee;
  }
  * { box-sizing: border-box; margin: 0; padding: 0; }
  html, body { width: 1200px; height: 987px; overflow: hidden; }
  body {
    background: var(--stage);
    font-family: "Open Sans", Arial, sans-serif;
    display: flex;
    flex-direction: column;
    align-items: center;
    justify-content: center;
    gap: 40px;
  }
  .card {
    position: relative;
    width: 780px;
    height: 446px;
    border-radius: 26px;
    overflow: hidden;
    box-shadow: 0 6px 18px rgba(0,0,0,.15);
  }

  /* Front */
  .card-front { background: var(--white); }
  .card-front .wave { position: absolute; inset: 0; }
  .brand {
    position: absolute;
    left: 44px;
    top: 70px;
    color: var(--ink);
  }
  .brand-name {
    font-size: 64px;
    font-weight: 300;
    letter-spacing: -1px;
    line-height: 1;
  }
  .brand-tagline {
    margin-top: 6px;
    padding-top: 4px;
    border-top: 2px solid #777;
    font-size: 22px;
    font-weight: 400;
    color: var(--text);
    letter-spacing: .3px;
  }
  .divider {
    position: absolute;
    left: 470px;
    top: 48px;
    width: 1px;
    height: 215px;
    background: var(--rule);
  }
  .contact {
    position: absolute;
    left: 492px;
    top: 62px;
    list-style: none;
    color: var(--text);
    font-size: 20px;
    line-height: 30px;
  }
  .contact li { display: flex; align-items: center; gap: 10px; }
  .contact .icon { width: 18px; height: 18px; flex: none; }
  .contact .address { margin-top: 8px; display: block; line-height: 27px; }
  .person {
    position: absolute;
    left: 500px;
    top: 360px;
    color: var(--white);
  }
  .person-name { font-size: 24px; font-weight: 700; line-height: 1.2; }
  .person-title { font-size: 18px; font-weight: 400; line-height: 1.3; }

  /* Back */
  .card-back {
    background: var(--ink);
    display: flex;
    flex-direction: column;
    align-items: center;
    justify-content: center;
    color: var(--white);
    gap: 30px;
  }
  .back-brand { display: flex; align-items: center; gap: 18px; }
  .back-brand .dot {
    width: 40px; height: 40px; border-radius: 50%;
    border: 6px solid var(--white);
  }
  .back-brand .name { font-size: 60px; font-weight: 300; letter-spacing: -1px; }
  .back-url { font-size: 20px; letter-spacing: 5px; font-weight: 400; }
</style>
</head>
<body>

  <section class="card card-front">
    <svg class="wave" viewBox="0 0 780 446" preserveAspectRatio="none" aria-hidden="true">
      <path fill="var(--red)" d="M0,196 C200,200 380,280 560,304 C660,316 730,318 780,318 L780,446 L0,446Z"/>
      <path fill="var(--white)" d="M0,226 C205,232 385,298 560,312 C660,322 730,324 780,324 L780,446 L0,446Z"/>
      <path fill="var(--ink)" d="M0,232 C210,240 390,303 560,316 C660,325 730,327 780,327 L780,446 L0,446Z"/>
      <path fill="var(--white)" d="M0,240 C215,250 395,309 560,320 C660,329 730,330 780,330 L780,446 L0,446Z"/>
      <path fill="var(--ink)" d="M0,250 C220,262 400,316 560,326 C660,333 730,334 780,334 L780,446 L0,446Z"/>
    </svg>

    <div class="brand">
      <div class="brand-name">RB Tolvane</div>
      <div class="brand-tagline">turning designs into spaces</div>
    </div>

    <div class="divider"></div>

    <ul class="contact">
      <li>
        <svg class="icon" viewBox="0 0 20 20"><circle cx="10" cy="10" r="10" fill="var(--red)"/><path d="M7 5l2 2-1 1.5c.6 1.4 1.7 2.5 3 3l1.5-1 2 2-1.3 1.5c-3.5-.3-7-3.8-7.2-7.3z" fill="var(--white)"/></svg>
        123-456-0789
      </li>
      <li>
        <svg class="icon" viewBox="0 0 20 20"><rect x="5" y="1" width="10" height="18" rx="2" fill="var(--red)"/><rect x="7" y="4" width="6" height="8" fill="var(--white)"/></svg>
        123-456-0789
      </li>
      <li>
        <svg class="icon" viewBox="0 0 20 20"><rect x="1" y="4" width="18" height="12" rx="2" fill="var(--red)"/><path d="M2 5l8 6 8-6" stroke="var(--white)" stroke-width="1.6" fill="none"/></svg>
        info@rbtolvane.com
      </li>
      <li>
        <svg class="icon" viewBox="0 0 20 20"><circle cx="10" cy="10" r="9" fill="var(--red)"/><path d="M1 10h18M10 1c-4 4-4 14 0 18M10 1c4 4 4 14 0 18" stroke="var(--white)" stroke-width="1.3" fill="none"/></svg>
        www.rbtolvane.com
      </li>
      <li class="address">Street Name, City Name<br>State Zip Code</li>
    </ul>

    <div class="person">
      <div class="person-name">Your Name</div>
      <div class="person-title">Title</div>
    </div>
  </section>

  <section class="card card-back">
    <div class="back-brand">
      <span class="dot"></span>
      <span class="name">RB Tolvane</span>
    </div>
    <div class="back-url">www.rbtolvane.com</div>
  </section>

</body>
</html>
```